Vernac Law Business cards and stationary design project

We are looking for a stationary design for business cards (double sided), 8x10, 5x7, and legal and standard envelopes.

We would like the design to match the logo that we have already.
Color palate preferred is Teal, White, grey and any others that will look good for a professional law firm.

We would like this statement: "RELATIONSHIPS. RESPECT. RESULT" to be on the back of the business cards and maybe on the stationary if it looks good.

Please see link to website for more information: www.vernac-law.example

Target Market(s)

Potential clients that need Attorney services.

Industry/Entity Type

Law Firm

Contact Information for Business Card

We would like the front and back to be two different colors. Current business cards are teal front, grey back and are a vertical design. We are open to options with colors.

Font styles to use
Serif

Colors
33a6d7
33b8a4
b9b9b9
5c5c5c

Requirements
Must have
• Logo supplied needs to go on the card and stationary.
• Match website color palate, www.vernac-law.example
• Be professional and not too wordy.
• Criminal Law, Civil Litigation, Personal Injury, Restraining Orders need to be on the card.
Nice to have
• RELATIONSHIPS. RESPECT. RESULTS. on the back of the card.
Should not have
• Not be too busy/wordy or too flashy.

```html
<!DOCTYPE html>
<html lang="en">
<head>
<meta charset="utf-8">
<title>Vernac Law — Stationery Set</title>
<link rel="stylesheet" href="https://fonts.googleapis.com/css2?family=Cinzel:wght@400;500&display=swap">
<style>
  :root {
    --backdrop: #d4d4d4;
    --paper: #ffffff;
    --teal: #13879a;
    --teal-line: #3b9fb0;
    --ink-grey: #555a5e;
    --band-grey: #5f6062;
    --shadow: 2px 3px 6px rgba(0,0,0,0.28);
  }
  * { box-sizing: border-box; margin: 0; padding: 0; }
  html, body { width: 1200px; height: 900px; overflow: hidden; }
  body {
    background: var(--backdrop);
    position: relative;
    font-family: "Cinzel", "Times New Roman", serif;
  }
  .sheet { position: absolute; background: var(--paper); box-shadow: var(--shadow); }

  .brand-name {
    font-family: "Cinzel", "Times New Roman", serif;
    font-weight: 400;
    color: var(--teal);
    letter-spacing: 0.04em;
    white-space: nowrap;
  }

  /* Envelope back */
  .envelope-back { left: 65px; top: 147px; width: 518px; height: 258px; }
  .envelope-back .flap { position: absolute; left: 0; top: 0; }

  /* Envelope front */
  .envelope-front { left: 121px; top: 260px; width: 518px; height: 258px; }
  .envelope-front .brand-name { position: absolute; left: 30px; top: 68px; font-size: 19px; }
  .envelope-front .return-address {
    position: absolute; left: 27px; top: 192px;
    font-size: 11.5px; line-height: 13px; color: var(--ink-grey);
  }
  .envelope-front .email {
    position: absolute; right: 32px; top: 229px;
    font-size: 10.5px; letter-spacing: 0.08em; color: var(--ink-grey);
  }

  /* Business card front */
  .card-front { left: 61px; top: 539px; width: 280px; height: 167px; }
  .card-front .brand-name { position: absolute; left: 22px; top: 78px; font-size: 16px; }
  .card-front .contact {
    position: absolute; left: 146px; top: 34px; height: 62px;
    border-left: 1px solid var(--teal-line); padding-left: 4px;
    font-size: 7.5px; line-height: 9px; color: var(--teal);
  }
  .card-front .contact .gap { height: 9px; }
  .practice-band {
    position: absolute; left: 0; bottom: 0; width: 100%; height: 38px;
    background: var(--band-grey); color: #fff; text-align: center;
    border-top: 2px solid #fff; outline: 1px solid #9a9a9a;
  }
  .practice-band .label { font-size: 8.5px; letter-spacing: 0.22em; margin-top: 7px; }
  .practice-band .areas { font-size: 6.4px; margin-top: 5px; letter-spacing: 0.02em; }

  /* Business card back */
  .card-back { left: 359px; top: 539px; width: 279px; height: 167px; background: var(--teal); }
  .card-back .tagline {
    position: absolute; left: 21px; top: 15px;
    font-size: 21px; line-height: 17px; color: #fff; letter-spacing: 0.04em;
  }
  .card-back .website {
    position: absolute; right: 20px; top: 142px;
    font-size: 8px; letter-spacing: 0.14em; color: #fff;
  }

  /* Letterhead */
  .letterhead { left: 669px; top: 118px; width: 471px; height: 665px; }
  .letterhead .brand-name { position: absolute; right: 20px; top: 68px; font-size: 17px; }
  .letterhead .footer {
    position: absolute; left: 32px; top: 616px; width: 407px; height: 32px;
    border-top: 1px solid var(--teal-line); border-bottom: 1px solid var(--teal-line);
    text-align: center; font-size: 6.6px; line-height: 11px; color: var(--ink-grey);
    padding-top: 5px;
  }
</style>
</head>
<body>

  <div class="sheet envelope-back">
    <svg class="flap" width="518" height="62" viewBox="0 0 518 62">
      <polygon points="0,0 518,0 483,62 33,62" fill="var(--teal)"/>
    </svg>
  </div>

  <div class="sheet envelope-front">
    <div class="brand-name">Vernac Law</div>
    <div class="return-address">
      Southern California,<br>
      482 Harbor View Ave. #210<br>
      Seabright Cove, CA 90299<br>
      (555) 014-2790
    </div>
    <div class="email">anna@vernac-law.example</div>
  </div>

  <div class="sheet card-front">
    <div class="brand-name">Vernac Law</div>
    <div class="contact">
      Southern California,<br>
      482 Harbor View Ave. #210<br>
      Seabright Cove, CA 90299
      <div class="gap"></div>
      (555) 014-2790<br>
      anna@vernac-law.example
    </div>
    <div class="practice-band">
      <div class="label">Practice Areas:</div>
      <div class="areas">Criminal Law &nbsp;|&nbsp; Civil Litigation/Personal Injury &nbsp;|&nbsp; Restraining Orders</div>
    </div>
  </div>

  <div class="sheet card-back">
    <div class="tagline">Relationships<br>Respect<br>Result</div>
    <div class="website">www.vernac-law.example</div>
  </div>

  <div class="sheet letterhead">
    <div class="brand-name">Vernac Law</div>
    <div class="footer">
      Southern California, 482 Harbor View Ave. #210 Seabright Cove, CA 90299<br>
      (555) 014-2790 &nbsp;|&nbsp; anna@vernac-law.example
    </div>
  </div>

</body>
</html>
```